Construction material supplies company business card ****

1. Full company name “K T Masonry Works Ltd”
I am after a Business card design for the company as a whole. We are better known in Solomon Islands as “K T Masonry” for short.

We are a building materials supplier of
Ready Mixed Concrete, Bricks and Blocks,
Quarry products- gravel, aggregates, sand etc.
Cement distributor/retailer of reputable brands.
Other prefab concrete products. Culverts, wave breakers, concrete retaining blocks etc.

2. Competitive Advantage over Competition: Quality, efficient, professional, dependable, reliable

3. We want people to feel trust worthy, high quality, strong when they see our brand

5. No preference to color. Maybe more sturdy and corporate. Not fancy.

Industry/Entity Type

CONSTRUCTION SUPPLY

Contact Information for Business Card

Name, Position, office phone mob phone, email

Requirements
Must have
• the company logo
Nice to have
• would like to see a mixture of designs, of with logo only and also with simple graphic designs to bring out the company whilst still have the strong sturdy professional feeling

```html
<!DOCTYPE html>
<html lang="en">
<head>
<meta charset="utf-8">
<title>K T Masonry – Business Card</title>
<link href="https://fonts.googleapis.com/css2?family=Arimo:wght@400;700&display=swap" rel="stylesheet">
<style>
  :root {
    --backdrop: #0c0c0e;
    --card: #2a2b2e;
    --card-edge: #1c5a8c;
    --brand-blue: #1d5f94;
    --text-light: #c9cacc;
    --rule: #47484c;
  }
  * { box-sizing: border-box; margin: 0; padding: 0; }
  html, body {
    width: 1200px; height: 820px; overflow: hidden;
    background: var(--backdrop);
    font-family: "Arimo", Arial, sans-serif;
  }
  .stage {
    position: relative; width: 1200px; height: 820px;
    display: flex; align-items: center; justify-content: center; gap: 40px;
  }
  .card {
    position: relative; width: 540px; height: 310px;
    background: var(--card);
    border-bottom: 3px solid var(--card-edge);
    border-left: 2px solid var(--card-edge);
    box-shadow: 0 18px 40px rgba(0,0,0,.6);
  }
  /* Front */
  .brand {
    position: absolute; display: flex; align-items: center; gap: 12px;
    color: var(--brand-blue); font-weight: 700; letter-spacing: 2px;
    text-transform: uppercase;
  }
  .front .brand { top: 48px; right: 44px; font-size: 30px; }
  .brand-square { width: 26px; height: 26px; background: var(--brand-blue); }
  .rule { position: absolute; height: 1px; background: var(--rule); }
  .rule-top { top: 100px; left: 250px; right: 40px; }
  .rule-name { top: 196px; left: 250px; right: 40px; }
  .person { position: absolute; left: 40px; top: 172px; }
  .person-name {
    color: var(--brand-blue); font-weight: 700; font-size: 20px;
    text-transform: uppercase; letter-spacing: .5px;
  }
  .person-role { color: var(--text-light); font-size: 15px; margin-top: 4px; }
  .phones { position: absolute; left: 40px; bottom: 34px; color: var(--text-light); font-size: 17px; }
  .web { position: absolute; right: 40px; top: 118px; color: var(--text-light); font-size: 15px; text-align: right; }
  .line { display: flex; align-items: center; gap: 8px; line-height: 24px; }
  .web .line { justify-content: flex-end; }
  .icon { width: 14px; height: 14px; flex: none; }
  /* Back */
  .back .brand {
    top: 50%; left: 50%; transform: translate(-50%, -50%);
    font-size: 40px; white-space: nowrap;
  }
  .back .brand-square { width: 36px; height: 36px; }
</style>
</head>
<body>
<main class="stage">
  <section class="card front" aria-label="Business card front">
    <div class="brand"><span class="brand-square"></span>K T Masonry</div>
    <div class="rule rule-top"></div>
    <div class="person">
      <p class="person-name">Daniel Harper</p>
      <p class="person-role">Managing Director</p>
    </div>
    <div class="rule rule-name"></div>
    <div class="phones">
      <p class="line">
        <svg class="icon" viewBox="0 0 16 16"><path d="M3 1h3l1.5 4-2 1.3a9 9 0 0 0 4.2 4.2L11 8.5l4 1.5v3a2 2 0 0 1-2 2A12 12 0 0 1 1 3a2 2 0 0 1 2-2z" fill="none" stroke="#1d5f94" stroke-width="1.5"/></svg>
        044-987 654 321
      </p>
      <p class="line">
        <svg class="icon" viewBox="0 0 16 16"><rect x="4" y="1" width="8" height="14" rx="1.5" fill="none" stroke="#1d5f94" stroke-width="1.5"/><circle cx="8" cy="12.5" r="0.9" fill="#1d5f94"/></svg>
        044-987 654 322
      </p>
    </div>
    <div class="web">
      <p class="line">info@ktmasonry.sb
        <svg class="icon" viewBox="0 0 16 16"><rect x="1" y="3" width="14" height="10" fill="#1d5f94"/><path d="M1 3l7 6 7-6" fill="none" stroke="#2a2b2e" stroke-width="1.3"/></svg>
      </p>
      <p class="line">www.ktmasonry.sb
        <svg class="icon" viewBox="0 0 16 16"><circle cx="8" cy="8" r="7" fill="#1d5f94"/><path d="M1 8h14M8 1c3 3.5 3 10.5 0 14M8 1c-3 3.5-3 10.5 0 14" fill="none" stroke="#2a2b2e" stroke-width="1"/></svg>
      </p>
    </div>
  </section>

  <section class="card back" aria-label="Business card back">
    <div class="brand"><span class="brand-square"></span>K T Masonry</div>
  </section>
</main>
</body>
</html>
```